Kestrelbrook Student Accomodation needs a business card design

Hi Guys,

We are a Student Accommodation company in Australia. We already have a logo which I will submit.

I will require the design of the business cards from you.

I am after something that looks clean, modern and that people feel interested and actually want to contact us.

We would like to see designs that are innovative.

On the business cards I will require to have:

Employee Name
Position
Phone number
Email
Facebook page

I hope you can help me with this project guys as I have heard really good things from you.

```html
<!DOCTYPE html>
<html lang="en">
<head>
<meta charset="utf-8">
<title>Kestrelbrook Student Accomodation – Business Card</title>
<link rel="stylesheet" href="https://fonts.googleapis.com/css2?family=Open+Sans:wght@400;700&display=swap">
<style>
  :root{
    --green:#0f9139;
    --gold:#f2b533;
    --white:#ffffff;
    --ink:#1c1c1c;
    --stage:#e9eaec;
  }
  *{box-sizing:border-box;margin:0;padding:0}
  html,body{width:1200px;height:680px;overflow:hidden}
  body{background:var(--stage);font-family:"Open Sans",Arial,sans-serif;color:var(--ink);position:relative}
  .card{position:absolute;top:190px;width:520px;height:300px;background:var(--white);border-radius:22px;overflow:hidden;box-shadow:0 6px 22px rgba(0,0,0,.18)}
  .card--front{left:50px}
  .card--back{left:630px}
  .card__swoosh{position:absolute;inset:0;width:100%;height:100%}
  .holder{position:absolute;top:22px;right:34px;text-align:right;line-height:1.15}
  .holder__name{color:var(--white);font-size:16px;font-weight:400;letter-spacing:.5px}
  .holder__role{color:var(--gold);font-size:13px}
  .brand{position:absolute;display:flex;align-items:center;gap:8px;color:var(--green);font-weight:700;line-height:1.1}
  .brand__mark{flex:none;background:var(--gold)}
  .card--front .brand{left:34px;top:190px;font-size:17px;width:230px}
  .card--front .brand__mark{width:16px;height:16px}
  .contacts{position:absolute;right:30px;top:176px;list-style:none;font-size:14px;line-height:1.45;text-align:right}
  .contacts li,.phone{display:flex;align-items:center;gap:7px;justify-content:flex-end}
  .phone{position:absolute;left:34px;bottom:24px;font-size:16px;letter-spacing:.5px}
  .icon{width:13px;height:13px;flex:none}
  .card--back .brand{left:0;right:0;top:104px;justify-content:center;font-size:26px;text-align:left}
  .card--back .brand__mark{width:26px;height:26px}
  .card--back .brand span{width:260px}
  .web{position:absolute;left:0;right:0;bottom:26px;text-align:center;font-size:15px;letter-spacing:1.5px}
</style>
</head>
<body>
  <section class="card card--front" aria-label="Business card front">
    <svg class="card__swoosh" viewBox="0 0 520 300" preserveAspectRatio="none" aria-hidden="true">
      <path d="M0 0H520V112Q300 40 0 160Z" fill="var(--green)"/>
      <path d="M0 160Q300 40 520 112V122Q300 58 0 178Z" fill="var(--gold)"/>
    </svg>
    <div class="holder">
      <p class="holder__name">Marcus Ellery</p>
      <p class="holder__role">manager</p>
    </div>
    <div class="brand"><span class="brand__mark"></span><span>Kestrelbrook Student Accomodation</span></div>
    <ul class="contacts">
      <li>
        <svg class="icon" viewBox="0 0 14 14" aria-hidden="true"><rect x="1" y="3" width="12" height="8" fill="none" stroke="var(--green)" stroke-width="1.6"/><path d="M1 3l6 5 6-5" fill="none" stroke="var(--green)" stroke-width="1.4"/></svg>
        info@kestrelbrook.com
      </li>
      <li>
        <svg class="icon" viewBox="0 0 14 14" aria-hidden="true"><circle cx="7" cy="7" r="6" fill="var(--green)"/></svg>
        facebook.com/kestrelbrook
      </li>
    </ul>
    <p class="phone">
      <svg class="icon" viewBox="0 0 14 14" aria-hidden="true"><path d="M3 1.5l2.2 2.5-1.2 1.6c.8 1.7 2 2.9 3.6 3.7l1.5-1.2 2.5 2.2-1.4 2c-4.8-.4-8.4-4-8.9-8.8z" fill="var(--green)"/></svg>
      040 555 0172
    </p>
  </section>

  <section class="card card--back" aria-label="Business card back">
    <div class="brand"><span class="brand__mark"></span><span>Kestrelbrook Student Accomodation</span></div>
    <p class="web">facebook.com/kestrelbrook</p>
  </section>
</body>
</html>
```